Need wine label for brand that is named: Kesavati Vineyards & Winery

Kesavati is a yoga way of breathing. In Sanskrit Kesavati means "flying up." I would like a creative wine label that articulates Kesavati. The label should include a graphic and the name Kesavati on one line and Vineyards & Winery in smaller print underneath Kesavati.

```html
<!DOCTYPE html>
<html lang="en">
<head>
<meta charset="utf-8">
<title>Kesavati Vineyards &amp; Winery – Pinot Noir Label</title>
<link rel="stylesheet" href="https://fonts.googleapis.com/css2?family=Fira+Sans+Condensed:wght@500;600&family=Rajdhani:wght@600;700&display=swap">
<style>
  :root {
    --blue-deep: #1a46a8;
    --blue-teal: #1590b0;
    --blue-mid: #1f6fb5;
    --ink: #343434;
    --paper: #ffffff;
  }
  * { margin: 0; padding: 0; box-sizing: border-box; }
  html, body { width: 943px; height: 1200px; overflow: hidden; background: var(--paper); }
  .label {
    position: relative;
    width: 943px;
    height: 1200px;
    background: var(--paper);
    font-family: "Rajdhani", sans-serif;
    color: var(--ink);
  }
  .band {
    position: absolute;
    left: 225px;
    width: 495px;
    background: linear-gradient(90deg, var(--blue-deep), var(--blue-teal) 50%, var(--blue-deep));
  }
  .band--top { top: 0; height: 52px; }
  .band--bottom {
    top: 1124px; height: 76px;
    display: flex; align-items: center; justify-content: center;
  }
  .abv {
    color: var(--paper);
    font-family: "Rajdhani", sans-serif;
    font-weight: 700;
    font-size: 31px;
    letter-spacing: 1px;
  }
  .brand {
    position: absolute;
    left: 225px; top: 54px; width: 495px;
    text-align: center;
    color: var(--blue-mid);
    font-family: "Rajdhani", sans-serif;
    font-weight: 600;
  }
  .brand__name { font-size: 112px; line-height: 1; letter-spacing: 3px; }
  .brand__sub { font-size: 27px; letter-spacing: 3px; margin-top: 2px; }

  .ornament { position: absolute; }
  .ornament--left {
    left: 22px; top: 290px; width: 200px; height: 602px;
    border-radius: 301px 0 0 301px / 301px 0 0 301px;
    background: linear-gradient(180deg, #5aaad0, #2a72c0 50%, #5aaad0);
  }
  .ornament--right {
    left: 722px; top: 290px; width: 200px; height: 602px;
    border-radius: 0 301px 301px 0 / 0 301px 301px 0;
    background: linear-gradient(180deg, #5aaad0, #2a72c0 50%, #5aaad0);
  }
  .ornament--center {
    left: 397px; top: 534px; width: 170px; height: 170px;
    border-radius: 50%;
    background: linear-gradient(135deg, var(--blue-teal), var(--blue-deep));
  }
  .frame-rule { position: absolute; top: 238px; }
  .frame-rule--left { left: 212px; }
  .frame-rule--right { left: 710px; }

  .text { position: absolute; left: 225px; width: 495px; text-align: center; }
  .varietal {
    top: 380px;
    font-family: "Fira Sans Condensed", sans-serif;
    font-weight: 600;
    font-size: 80px;
    line-height: 1;
  }
  .vintage { top: 814px; font-size: 52px; font-weight: 700; letter-spacing: 8px; line-height: 1; padding-left: 8px; }
  .series { top: 900px; font-size: 50px; font-weight: 700; letter-spacing: 10px; line-height: 1; padding-left: 10px; }
  .region {
    top: 996px;
    font-family: "Fira Sans Condensed", sans-serif;
    font-weight: 600;
    font-size: 36px;
    line-height: 1;
    color: #222;
  }
</style>
</head>
<body>
<main class="label">
  <div class="band band--top"></div>

  <header class="brand">
    <div class="brand__name">Kesavati</div>
    <div class="brand__sub">Vineyards &amp; Winery</div>
  </header>

  <div class="ornament ornament--left" role="img" aria-label="Half mandala ornament in blue line work, rising petals suggesting flight"></div>
  <div class="ornament ornament--right" role="img" aria-label="Half mandala ornament in blue line work, rising petals suggesting flight"></div>

  <svg class="frame-rule frame-rule--left" width="20" height="716" viewBox="0 0 20 716" aria-hidden="true">
    <defs>
      <linearGradient id="ruleGrad" x1="0" y1="0" x2="0" y2="1">
        <stop offset="0" stop-color="#1590b0"/>
        <stop offset="0.5" stop-color="#1f6fb5"/>
        <stop offset="1" stop-color="#1590b0"/>
      </linearGradient>
    </defs>
    <rect x="8.5" y="10" width="3" height="696" fill="url(#ruleGrad)"/>
    <polygon points="10,0 20,18 10,36 0,18" fill="#1f6fb5"/>
    <polygon points="10,676 20,694 10,716 0,694" fill="#1f6fb5"/>
  </svg>
  <svg class="frame-rule frame-rule--right" width="20" height="716" viewBox="0 0 20 716" aria-hidden="true">
    <rect x="8.5" y="10" width="3" height="696" fill="url(#ruleGrad)"/>
    <polygon points="10,0 20,18 10,36 0,18" fill="#1590b0"/>
    <polygon points="10,676 20,694 10,716 0,694" fill="#1590b0"/>
  </svg>

  <h1 class="text varietal">Pinot Noir</h1>
  <div class="ornament ornament--center" role="img" aria-label="Small lotus mandala motif"></div>
  <p class="text vintage">2014</p>
  <p class="text series">COLLECTION</p>
  <p class="text region">Napa Valley</p>

  <footer class="band band--bottom">
    <span class="abv">11.8% alc/vol.</span>
  </footer>
</main>
</body>
</html>
```